Window Treatment business needs website redesigned.

We need a revamp and refresh of our current site www.velmarix.ca
Looking to attract very high end customer. It should be a very simple design with very little text. This site will be visited by prospective homeowners, designers, builders and architects. They should feel that they are dealing with a high-end product selection, where experience, customer service and unique product offering is the focus. The content will be to highlight our services and highlight the manufacturers we sell, using a few rich photos to highlight the products. We should NOT look like we are a very large company. It should NOT have discounts/savings buttons and many menus to choose from. We offer over 15 years experience to narrow the many market options, to provide the right technical solution.
We specialize in products that are not readily available on the market and specifically motorized systems for indoors and outdoors.
Our main suppliers are Kravenholt.com, Dimbrell.com
We carry our own locally manufactured product line of roller shades.
Main product pictures should be of roller shades, outdoor bug screens, awnings and outdoor pergolas.

Reason: I understand that Christmas is coming up real short and many people are extremely busy. If you have a CREATIVE gifting you still want to submit, I look forward to your idea!

Reason: Due to holiday season, we have not had sufficient time to review to make a final decision. Thank you for your patience!

Target Market(s)

High end home owners, designers, builders, architects

Industry/Entity Type

Contractor

Coding

Coded - Design and coding required

Number of Pages Required

3 page

Font styles to use
Sans Serif

Requirements
Must have
• Landing page with full size image like homepage of zolvane.it
• Products page that highlights products with simple product shot image, description and link to manufacturer.
• On main page a scrolling of customer reviews.
• I want a very simple, eye-catching, emotional image for homepage. It does not need to include any product image.
• An image that shows technology combining/meshing with hand craftsmanship.
• Focus is on design.
• http://www.zolvane.it/en/gallery is a great layout and design.
Nice to have
• Logo shape for icons and watermark should be used.
• Look like and have simple motion effects like quorix.com or telvarin.com
Should not have
• Generic/standard looking feel like bluppet.com or mecklorwindow.ca
• No use of green as background only subtle text.
• Lots of text and pages.

```html
<!DOCTYPE html>
<html lang="en">
<head>
<meta charset="utf-8">
<title>Velmarix — Our Services</title>
<link rel="stylesheet" href="https://fonts.googleapis.com/css2?family=Montserrat:wght@400;500;600;700&display=swap">
<style>
:root{
  --page:#f8f8f8;
  --ink:#1e1e1e;
  --ink-soft:#444444;
  --muted:#6e6e6e;
  --green:#6ab743;
  --tile-grey:#dcdcdc;
  --tile-light:#ececec;
  --rule:#bdbdbd;
  --footer:#ffffff;
  --social:#8a8a8a;
}
*{box-sizing:border-box;margin:0;padding:0}
html,body{width:1200px;height:729px;overflow:hidden;background:var(--page);font-family:"Montserrat",Arial,sans-serif;color:var(--ink)}
.site{position:relative;width:1200px;height:729px}

.header{position:absolute;left:0;top:0;width:1200px;height:108px}
.brand{position:absolute;left:180px;top:25px;display:flex;align-items:center;gap:12px}
.brand-mark{width:66px;height:66px;border-radius:50%;border:4px solid var(--ink)}
.brand-name{font-size:33px;font-weight:500;color:var(--ink);letter-spacing:.3px}
.contact{position:absolute;right:210px;top:11px;display:flex;gap:18px;font-size:12px;align-items:center}
.contact span{display:flex;align-items:center;gap:8px}
.nav{position:absolute;right:210px;top:52px;display:flex;align-items:center;font-size:12px;font-weight:500}
.nav a{color:var(--ink);text-decoration:none;padding:6px 17px;border-radius:14px}
.nav .sep{padding:0 4px}
.nav a.active{background:var(--green);color:#fff}

.section-title{position:absolute;left:0;right:0;top:110px;height:26px;display:flex;align-items:center;justify-content:center}
.section-title::before,.section-title::after{content:"";flex:1;height:1px;background:var(--rule)}
.section-title h1{font-size:20px;font-weight:700;color:var(--green);padding:0 24px;letter-spacing:.5px}

.services{position:absolute;left:0;top:144px;width:1200px;height:414px;display:grid;grid-template-columns:repeat(4,300px);grid-template-rows:repeat(2,207px)}
.photo{width:100%;height:100%}
.p1{background:linear-gradient(160deg,#8aa6c4 0%,#b9c2c6 40%,#6e7d58 100%)}
.p2{background:linear-gradient(200deg,#e6eef8 0%,#8fb1e0 40%,#6f8fc4 100%)}
.p3{background:linear-gradient(180deg,#a88a62 0%,#c8a873 45%,#6f8a4c 100%)}
.p4{background:linear-gradient(120deg,#4a4a46 0%,#c9c4b8 45%,#8fa6c6 100%)}
.service{background:var(--tile-grey);padding:0 26px 0 29px}
.service h2{font-size:17.5px;font-weight:600;letter-spacing:.4px;margin-bottom:10px;color:var(--ink)}
.service p{font-size:11px;line-height:27px;text-align:justify;color:var(--ink-soft)}
.service.featured{background:var(--tile-light);padding-top:28px}
.service.featured h2{color:var(--green)}
.service.top-right{padding-top:37px}
.service.bottom-left{padding-top:31px}
.service.bottom-mid{padding-top:40px}

.partners{position:absolute;left:0;top:558px;width:1200px;height:110px;display:flex;align-items:center;justify-content:center;gap:58px}
.partner{font-size:25px;font-weight:600;color:var(--ink);letter-spacing:.3px}

.footer{position:absolute;left:0;top:669px;width:1200px;height:60px;background:var(--footer)}
.copyright{position:absolute;left:163px;top:23px;font-size:11px;color:var(--muted)}
.social{position:absolute;left:924px;top:16px;display:flex;gap:2px}
.social span{width:28px;height:28px;border-radius:50%;background:var(--social)}
</style>
</head>
<body>
<div class="site">
  <header class="header">
    <div class="brand"><span class="brand-mark"></span><span class="brand-name">Velmarix</span></div>
    <div class="contact">
      <span><svg width="10" height="16" viewBox="0 0 10 16"><rect x="1" y="1" width="8" height="14" rx="1.5" fill="none" stroke="#1e1e1e" stroke-width="1.2"/><line x1="4" y1="13" x2="6" y2="13" stroke="#1e1e1e"/></svg>416-555-0142</span>
      <span><svg width="16" height="11" viewBox="0 0 16 11"><rect x=".6" y=".6" width="14.8" height="9.8" fill="none" stroke="#1e1e1e" stroke-width="1.1"/><path d="M.6 .6 8 6 15.4 .6" fill="none" stroke="#1e1e1e" stroke-width="1.1"/></svg>info@velmarix.com</span>
    </div>
    <nav class="nav">
      <a href="#">Home</a><span class="sep">-</span>
      <a href="#">About Us</a><span class="sep">-</span>
      <a href="#" class="active">Services</a><span class="sep">-</span>
      <a href="#">Contact Us</a>
    </nav>
  </header>

  <div class="section-title"><h1>OUR SERVICES</h1></div>

  <main class="services">
    <div class="photo p1" role="img" aria-label="Outdoor pergola with retractable fabric roof overlooking green hills"></div>
    <article class="service featured"><h2>LORIUM IPSUM</h2><p>Ut enim ad minima veniam, quis nostrum exercitationem ullam corporis suscipit laboriosam, nisi ut aliquid ex ea commodi consequatur</p></article>
    <div class="photo p2" role="img" aria-label="Sunlit balcony awning against a bright blue sky"></div>
    <article class="service top-right"><h2>LORIUM IPSUM</h2><p>Ut enim ad minima veniam, quis nostrum exercitationem ullam corporis suscipit laboriosam, nisi ut aliquid ex ea commodi consequatur</p></article>
    <article class="service bottom-left"><h2>LORIUM IPSUM</h2><p>Ut enim ad minima veniam, quis nostrum exercitationem ullam corporis suscipit laboriosam, nisi ut aliquid ex ea commodi consequatur</p></article>
    <div class="photo p3" role="img" aria-label="Terrace with awning and lowered outdoor screen shade above a lake view"></div>
    <article class="service bottom-mid"><h2>LORIUM IPSUM</h2><p>Ut enim ad minima veniam, quis nostrum exercitationem ullam corporis suscipit laboriosam, nisi ut aliquid ex ea commodi consequatur</p></article>
    <div class="photo p4" role="img" aria-label="Apartment balconies fitted with vertical outdoor screens"></div>
  </main>

  <section class="partners" aria-label="Manufacturers we carry">
    <span class="partner">Dimbrell</span>
    <span class="partner">Sunmere</span>
    <span class="partner">Quietrail</span>
    <span class="partner">Halvern</span>
  </section>

  <footer class="footer">
    <p class="copyright">Copyrights © 2016, Norvade 360. All Rights Reserved.</p>
    <div class="social"><span></span><span></span><span></span><span></span></div>
  </footer>
</div>
</body>
</html>
```